Barrister at Law needs Business Card Design

Need a business card design for Barrister at Law. Double sided. Simple Neil Thorsby and Barrister at Law on one side with contact details on the other side. I would like a professional design using Black or Platinum. Details on reverse side would include qualifications - Bcom-Llb and Acc Spec Commercial Litigation. I have attached the logo. Contact details would include address/ Po Box/ Phone/Fax/Mobile/email. I would like to use raised print or spot gloss.

```html
<!DOCTYPE html>
<html lang="en">
<head>
<meta charset="utf-8">
<title>Neil Thorsby – Barrister at Law business card</title>
<link rel="stylesheet" href="https://fonts.googleapis.com/css2?family=Cinzel:wght@400;500&family=Open+Sans:wght@400;700&display=swap">
<style>
  :root {
    --backdrop: #e6e4e1;
    --card: #2b2b2d;
    --card-shade: #252527;
    --blue: #1f7ac4;
    --grey: #9c9c9c;
    --text: #b8b8b8;
  }
  * { margin: 0; padding: 0; box-sizing: border-box; }
  html, body { width: 1200px; height: 1000px; overflow: hidden; }
  body { background: var(--backdrop); position: relative; font-family: "Open Sans", Arial, sans-serif; }

  .card {
    position: absolute; left: 265px; width: 665px; height: 397px;
    background: var(--card); border-radius: 22px;
  }
  .card--front { top: 73px; }
  .card--back { top: 533px; }

  /* front */
  .brand { position: absolute; left: 40px; top: 72px; display: flex; align-items: center; }
  .brand__dot { width: 54px; height: 54px; border-radius: 50%; background: var(--blue); margin-right: 50px; }
  .brand__name { font-family: "Cinzel", Georgia, serif; font-weight: 500; font-size: 31px; color: var(--blue); letter-spacing: 1px; line-height: 1; }
  .brand__role { position: absolute; left: 144px; top: 106px; font-family: "Cinzel", Georgia, serif; font-size: 17px; color: var(--grey); letter-spacing: 4px; }

  .contact { position: absolute; left: 143px; top: 168px; color: var(--text); font-size: 16px; line-height: 20px; }
  .contact__name { font-weight: 700; font-size: 20px; color: var(--blue); line-height: 24px; }
  .contact__title { margin-bottom: 16px; }
  .contact__address { margin-bottom: 6px; }
  .contact__line { display: flex; align-items: center; height: 22px; }
  .contact__line svg { width: 14px; height: 14px; margin-right: 7px; fill: var(--blue); }

  .emboss {
    position: absolute; left: 430px; top: 115px; width: 190px; height: 190px; border-radius: 50%;
    background: var(--card-shade);
    box-shadow: inset 2px 2px 4px rgba(0,0,0,.5), inset -2px -2px 3px rgba(255,255,255,.05);
  }

  /* back */
  .seal { position: absolute; left: 0; right: 0; top: 95px; text-align: center; }
  .seal__dot {
    width: 78px; height: 78px; border-radius: 50%; margin: 0 auto 18px;
    background: var(--card-shade);
    box-shadow: inset 2px 2px 4px rgba(0,0,0,.5), inset -2px -2px 3px rgba(255,255,255,.05);
  }
  .seal__name { font-family: "Cinzel", Georgia, serif; font-weight: 500; font-size: 32px; color: var(--blue); letter-spacing: 3px; }
  .seal__role { font-family: "Cinzel", Georgia, serif; font-size: 22px; color: var(--grey); letter-spacing: 4px; margin-top: 6px; }
  .qualifications { position: absolute; left: 0; right: 0; top: 338px; text-align: center; color: var(--text); font-size: 16px; }
</style>
</head>
<body>
  <section class="card card--front">
    <div class="brand">
      <span class="brand__dot"></span>
      <span class="brand__name">NEIL THORSBY</span>
    </div>
    <div class="brand__role">BARRISTER AT LAW</div>

    <div class="contact">
      <div class="contact__name">CLARA HENSLEY</div>
      <div class="contact__title">LLB Acc. Spec. (Fam.)</div>
      <div class="contact__address">Unit 4/17 Quay Lane<br>BRISBANE Qld 4000</div>
      <div class="contact__line">
        <svg viewBox="0 0 14 14"><path d="M4 0h6a1 1 0 0 1 1 1v12a1 1 0 0 1-1 1H4a1 1 0 0 1-1-1V1a1 1 0 0 1 1-1zm.5 1.5v10h5v-10z"/></svg>
        + 000 000 0000
      </div>
      <div class="contact__line">
        <svg viewBox="0 0 14 14"><path d="M1 4c2-3 10-3 12 0l-1 2-3-1V4H5v1L2 6zM3 7h8l1 6H2z"/></svg>
        + 000 000 0000
      </div>
      <div class="contact__line">
        <svg viewBox="0 0 14 14"><path d="M3 1h8v4H3zM1 6h12v5h-2v2H3v-2H1zm3 3v3h6V9z"/></svg>
        + 000 000 0000
      </div>
      <div class="contact__line">
        <svg viewBox="0 0 14 14"><path d="M0 3h14v1L7 8 0 4zm0 2.5 7 4 7-4V11H0z"/></svg>
        info@thorsbylaw.com
      </div>
    </div>

    <div class="emboss" aria-hidden="true"></div>
  </section>

  <section class="card card--back">
    <div class="seal">
      <div class="seal__dot"></div>
      <div class="seal__name">NEIL THORSBY</div>
      <div class="seal__role">BARRISTER AT LAW</div>
    </div>
    <div class="qualifications">Bcom-Llb and Acc Spec Commercial Litigation</div>
  </section>
</body>
</html>
```